Tidal Forge - Crypto Currency Miner Powered by Renewable Energy Website

We Need Web Pages Design for Website for Crypto Currency Miner

Serivices include:
Mining Rig Sales
Housing for Rigs turnkey on renewable energy grid
Cloud Mining term packages
Updates

http://www.vaultrigsurvey.example (Competitors sites)

Target Market(s)

Investers for Mining Rigs and terms for 1,2 or 3 years of Hash rate

Industry/Entity Type

Mining

Number of Pages Required

5+ page

Font styles to use
Sans Serif

Colors
add136
9bcb3c
606060
474747
ffc214
cadf82
fbee3e
876aae
6b449b

Requirements
Must have
• Pictures of Solar, Wind and power Factor Correction units
Nice to have
• e-commerce platform so contract terms can be purchased through website
Should not have
• Heavy construction equipment

```html
<!DOCTYPE html>
<html lang="en">
<head>
<meta charset="utf-8">
<title>Tidal Forge — Renewable Crypto Mining</title>
<link rel="stylesheet" href="https://fonts.googleapis.com/css2?family=Open+Sans:wght@300;400;600;700;800&display=swap">
<style>
:root{
  --green:#2a9d49;
  --green-light:#9bcb3c;
  --text:#474747;
  --muted:#606060;
  --grey-band:#e7e4e1;
  --dark:#262626;
  --darker:#1b1b1b;
  --white:#ffffff;
}
*{box-sizing:border-box;margin:0;padding:0}
html,body{width:1200px;height:5263px;overflow:hidden}
body{font-family:'Open Sans',Arial,sans-serif;color:var(--text);background:var(--white);position:relative}
.section{position:absolute;left:0;width:1200px}
.abs{position:absolute}
.center{text-align:center;left:0;width:1200px}
.btn{position:absolute;background:var(--green);color:var(--white);font-size:12px;font-weight:700;letter-spacing:.5px;border-radius:16px;text-align:center;line-height:32px;height:32px}
.section-title{position:absolute;left:0;width:1200px;text-align:center;font-size:36px;font-weight:400;color:var(--text)}
.section-title b{color:var(--green);font-weight:400}
.rule{position:absolute;left:585px;width:30px;height:2px;background:var(--green)}
.lead{position:absolute;left:300px;width:600px;text-align:center;font-size:13px;line-height:20px;color:var(--muted)}
.placeholder{position:absolute}

/* top bar + header */
.topbar{top:0;height:28px;background:#1f1f1f;color:#bbb;font-size:11px}
.topbar .left{left:90px;top:7px}
.topbar .right{right:90px;top:7px;word-spacing:14px}
.header{top:28px;height:112px;background:var(--white);box-shadow:0 1px 4px rgba(0,0,0,.08)}
.brand{left:88px;top:24px;display:flex;align-items:center;gap:10px}
.brand-dot{width:44px;height:44px;border-radius:50%;background:var(--green)}
.brand-name{font-size:24px;font-weight:700;color:var(--text)}
.nav{left:628px;top:64px;display:flex;gap:23px;font-size:15px;font-weight:600;color:var(--text)}
.nav .active{color:var(--green);border-bottom:2px solid var(--green)}
.quote-btn{left:1000px;top:22px;width:100px;height:30px;line-height:30px;border-radius:3px;font-size:11px}

/* hero */
.hero{top:140px;height:562px}
.hero .placeholder{left:0;top:0;width:1200px;height:562px;background:linear-gradient(160deg,#8fb3d6 0%,#4d76a8 45%,#274a7c 100%)}
.hero-text{left:255px;top:200px;color:var(--white)}
.hero-text .small{font-size:40px;font-weight:600}
.hero-text .big{font-size:64px;font-weight:700;line-height:70px}
.hero-text .mid{font-size:58px;font-weight:400;line-height:64px}
.dots{display:flex;gap:10px}
.dots span{width:9px;height:9px;border-radius:50%;background:#bbb}
.dots span.on{background:var(--green)}

/* about */
.about{top:702px;height:526px}
.about .placeholder{left:123px;top:98px;width:438px;height:305px;background:linear-gradient(180deg,#8a8f95,#6b6153 60%,#544636)}
.about h2{left:632px;top:98px;font-size:34px;font-weight:400}
.about h2 b{color:var(--green);font-weight:600}
.about .p1{left:632px;top:160px;width:490px;font-size:14px;font-weight:600;line-height:20px}
.about .p2{left:632px;top:222px;width:490px;font-size:12px;line-height:18px;color:var(--muted)}
.about .btn{left:632px;top:368px;width:160px}

/* services */
.services{top:1228px;height:744px;background:var(--grey-band)}
.svc{position:absolute;top:290px;width:330px;text-align:center}
.svc .icon{width:126px;height:126px;border-radius:50%;background:var(--green);margin:0 auto}
.svc h3{margin-top:32px;font-size:20px;font-weight:400}
.svc p{margin:14px auto 0;width:260px;font-size:12px;line-height:18px;color:var(--muted)}

/* cta */
.cta{top:1972px;height:204px;background:var(--green);color:var(--white)}
.cta .kicker{top:30px;font-size:12px}
.cta .headline{top:54px;font-size:28px;font-weight:700}
.cta .btn{left:515px;top:120px;width:170px;background:var(--white);color:var(--green)}

/* experts */
.experts{top:2176px;height:870px}
.expert{position:absolute;top:263px;width:288px;text-align:center}
.expert .placeholder{position:static;width:288px;height:379px;background:linear-gradient(180deg,#e2e2e2,#b9bcc2 60%,#4a4f5c)}
.expert h4{margin-top:36px;font-size:17px;font-weight:400}
.expert span{display:block;margin-top:6px;font-size:11px;font-weight:700;color:var(--green)}

/* question */
.question{top:3046px;height:593px;background:radial-gradient(ellipse at 50% 40%,#3a3a3a,#202020 75%);color:var(--white)}
.question .section-title{color:var(--white)}
.field-label{position:absolute;font-size:12px;font-weight:600}
.field{position:absolute;background:var(--white);height:28px}
.send{left:510px;top:481px;width:150px;background:var(--white);color:var(--text)}

/* news */
.news{top:3639px;height:642px}
.card{position:absolute;top:203px;width:298px;height:369px;border:1px solid #ddd;background:var(--white)}
.card .placeholder{position:static;width:296px;height:200px;background:linear-gradient(150deg,#d9dde2,#9aa3ae 55%,#4d5866)}
.card h5{margin:14px 14px 0;font-size:15px;font-weight:700;line-height:19px}
.card .date{margin:6px 14px 0;font-size:11px;color:var(--green)}
.card p{margin:8px 14px 0;font-size:11px;line-height:16px;color:var(--muted)}
.card .more{margin:10px 14px 0;font-size:11px;color:var(--green)}

/* newsletter */
.newsletter{top:4281px;height:147px;background:var(--green);color:var(--white)}
.newsletter .label{left:140px;top:52px;font-size:32px;font-weight:300}
.newsletter .label b{font-weight:700}
.newsletter .input{left:646px;top:48px;width:309px;height:48px;border:1px solid rgba(255,255,255,.8);font-size:12px;padding:15px 14px}
.newsletter .submit{left:961px;top:48px;width:162px;height:48px;background:var(--white);color:var(--text);font-size:13px;text-align:center;line-height:48px}

/* feedback */
.feedback{top:4428px;height:407px}
.avatar{left:307px;top:202px;width:60px;height:60px;border-radius:50%;background:linear-gradient(180deg,#c9a58c,#7a5a49)}
.feedback .who{left:277px;top:270px;width:120px;text-align:center;font-size:15px}
.feedback .who span{display:block;font-size:10px;font-weight:700;color:var(--green)}
.feedback .quote{left:484px;top:205px;width:570px;font-size:12px;line-height:20px;color:var(--muted);text-align:center}
.arrow{position:absolute;top:216px;font-size:22px;color:#888}

/* footer */
.footer{top:4835px;height:393px;background:var(--darker);color:#ccc;font-size:12px}
.footer h6{position:absolute;top:72px;font-size:16px;font-weight:700;color:var(--green);letter-spacing:.5px}
.footer .vline{position:absolute;top:72px;width:1px;height:260px;background:#444}
.footer ul{position:absolute;list-style:none;line-height:30px}
.post{position:absolute;left:642px;display:flex;gap:12px;width:250px}
.post .thumb{width:52px;height:48px;background:linear-gradient(135deg,#c9a13a,#6d5412)}
.post .t{font-size:11px;line-height:15px}
.post .t b{display:block;color:var(--green);font-weight:400}
.social{position:absolute;left:933px;top:120px;display:flex;gap:14px}
.social span{width:18px;height:18px;border-radius:50%;background:#ccc}
.copyright{top:5228px;height:35px;background:#111;color:#999;font-size:11px;text-align:center;line-height:35px}
</style>
</head>
<body>

<div class="section topbar">
  <div class="abs left">416 555 0192 &nbsp;|&nbsp; Info center</div>
  <div class="abs right">Services Pay&nbsp;Tabs Contact Whitepaper</div>
</div>

<header class="section header">
  <div class="abs brand"><div class="brand-dot"></div><div class="brand-name">Tidal Forge</div></div>
  <nav class="abs nav">
    <span class="active">Home</span><span>About</span><span>Team</span><span>Services</span><span>Products</span><span>Clients</span><span>Contact</span>
  </nav>
  <svg class="abs" style="left:912px;top:28px" width="40" height="18" viewBox="0 0 40 18">
    <circle cx="6" cy="7" r="5" fill="none" stroke="#474747" stroke-width="2"/><line x1="10" y1="11" x2="14" y2="15" stroke="#474747" stroke-width="2"/>
    <circle cx="32" cy="6" r="4" fill="#474747"/><path d="M25 17 a7 6 0 0 1 14 0z" fill="#474747"/>
  </svg>
  <div class="btn quote-btn">GET A QUOTE</div>
</header>

<section class="section hero">
  <div class="placeholder" role="img" aria-label="Rows of solar panels under a blue sky"></div>
  <div class="abs hero-text">
    <div class="small">With us</div>
    <div class="big">Mining equipment run</div>
    <div class="mid">Greener &amp; more efficient</div>
  </div>
  <div class="abs dots" style="left:520px;top:510px"><span class="on"></span><span></span><span></span></div>
</section>

<section class="section about">
  <div class="placeholder" role="img" aria-label="Wind turbines and solar field powering a rig facility"></div>
  <h2 class="abs">About <b>Tidal Forge</b></h2>
  <p class="abs p1">Lorem ipsum dolor sit amet, consectetur adipiscing elit, sed do eiusmod tempor incididunt ut labore et dolore magna aliqua.</p>
  <p class="abs p2">Ut enim ad minim veniam, quis nostrud exercitation ullamco laboris nisi ut aliquip ex ea commodo consequat. Duis aute irure dolor in reprehenderit in voluptate velit esse cillum dolore eu fugiat nulla pariatur. Lorem ipsum dolor sit amet, consectetur adipiscing elit, sed do eiusmod tempor incididunt ut labore et dolore magna aliqua. Sed ut perspiciatis unde omnis iste natus error sit voluptatem accusantium doloremque laudantium, totam rem aperiam quis autem vel eum iure.</p>
  <div class="btn">READ MORE</div>
</section>

<section class="section services">
  <h2 class="section-title" style="top:92px"><b>Services</b> We Provide</h2>
  <div class="rule" style="top:150px"></div>
  <p class="lead" style="top:190px;left:200px;width:800px">Ut enim ad minim veniam, quis nostrud exercitation ullamco laboris nisi ut aliquip ex ea commodo consequat. Duis aute irure dolor in reprehenderit in voluptate velit esse cillum dolore eu fugiat nulla pariatur.</p>
  <div class="svc" style="left:116px">
    <svg class="icon" viewBox="0 0 126 126" style="display:block"><circle cx="63" cy="63" r="63" fill="#2a9d49"/><circle cx="63" cy="63" r="22" fill="none" stroke="#fff" stroke-width="4"/><path d="M66 48 l-10 17 h9 l-4 14 l12-19 h-9z" fill="#fff"/><g stroke="#fff" stroke-width="4" stroke-linecap="round"><line x1="63" y1="28" x2="63" y2="34"/><line x1="63" y1="92" x2="63" y2="98"/><line x1="28" y1="63" x2="34" y2="63"/><line x1="92" y1="63" x2="98" y2="63"/><line x1="38" y1="38" x2="42" y2="42"/><line x1="84" y1="84" x2="88" y2="88"/><line x1="88" y1="38" x2="84" y2="42"/><line x1="38" y1="88" x2="42" y2="84"/></g></svg>
    <h3>Sed ut perspiciatis</h3>
    <p>Nemo enim ipsam voluptatem quia voluptas sit aspernatur aut odit aut fugit, sed quia magni.</p>
  </div>
  <div class="svc" style="left:446px">
    <svg class="icon" viewBox="0 0 126 126" style="display:block"><circle cx="63" cy="63" r="63" fill="#2a9d49"/><g fill="#fff"><rect x="61" y="58" width="4" height="42"/><path d="M63 58 L58 26 L66 26z"/><path d="M63 58 L92 72 L88 78z"/><path d="M63 58 L36 76 L33 70z"/><circle cx="63" cy="58" r="5"/></g></svg>
    <h3>error sit voluptatem</h3>
    <p>Nemo enim ipsam voluptatem quia voluptas sit aspernatur aut odit aut fugit, sed quia magni.</p>
  </div>
  <div class="svc" style="left:775px">
    <svg class="icon" viewBox="0 0 126 126" style="display:block"><circle cx="63" cy="63" r="63" fill="#2a9d49"/><rect x="34" y="48" width="54" height="30" rx="3" fill="none" stroke="#fff" stroke-width="4"/><rect x="90" y="56" width="5" height="14" fill="#fff"/><g fill="#fff"><rect x="40" y="54" width="8" height="18"/><rect x="51" y="54" width="8" height="18"/><rect x="62" y="54" width="8" height="18"/><rect x="73" y="54" width="8" height="18"/></g></svg>
    <h3>veritatis et quasi</h3>
    <p>Nemo enim ipsam voluptatem quia voluptas sit aspernatur aut odit aut fugit, sed quia magni.</p>
  </div>
  <div class="btn" style="left:530px;top:606px;width:160px">MORE SERVICES</div>
</section>

<section class="section cta">
  <div class="abs center kicker">ARE YOU INTEREST WITH US?</div>
  <div class="abs center headline">SED UT PERSPICIATIS UNDE OMNIS ISTE NATUS ERROR SIT</div>
  <div class="btn">MORE SERVICES</div>
</section>

<section class="section experts">
  <h2 class="section-title" style="top:66px">Our <b>Experts</b></h2>
  <div class="rule" style="top:124px"></div>
  <p class="lead" style="top:158px">Nemo enim ipsam voluptatem quia voluptas sit aspernatur aut odit aut fugit, sed quia consequuntur magni dolores eos qui ratione voluptatem sequi nesciunt.</p>
  <div class="expert" style="left:98px"><div class="placeholder" role="img" aria-label="Portrait of a senior advisor in a suit"></div><h4>Rowan</h4><span>BROKER</span></div>
  <div class="expert" style="left:404px"><div class="placeholder" role="img" aria-label="Portrait of a consultant in a suit"></div><h4>TOBIAS</h4><span>CONSULTANT</span></div>
  <div class="expert" style="left:719px"><div class="placeholder" role="img" aria-label="Portrait of a realtor in a jacket"></div><h4>CALLUM</h4><span>REALTOR</span></div>
  <div class="abs dots" style="left:585px;top:760px"><span class="on"></span><span></span></div>
</section>

<section class="section question">
  <h2 class="section-title" style="top:80px;color:#fff">Any <b>Question?</b></h2>
  <div class="field-label" style="left:158px;top:190px">NAME</div>
  <div class="field" style="left:158px;top:211px;width:397px"></div>
  <div class="field-label" style="left:158px;top:260px">EMAIL</div>
  <div class="field" style="left:158px;top:281px;width:397px"></div>
  <div class="field-label" style="left:158px;top:330px">PHONE</div>
  <div class="field" style="left:158px;top:351px;width:397px"></div>
  <div class="field-label" style="left:614px;top:190px">TOPIC</div>
  <div class="field" style="left:614px;top:211px;width:396px"></div>
  <div class="field-label" style="left:614px;top:260px">QUESTIONS</div>
  <div class="field" style="left:614px;top:281px;width:396px;height:95px"></div>
  <div class="btn send">SEND NOW</div>
</section>

<section class="section news">
  <h2 class="section-title" style="top:40px">Latest <b>News</b></h2>
  <div class="rule" style="top:98px"></div>
  <p class="lead" style="top:132px">Nemo enim ipsam voluptatem quia voluptas sit aspernatur aut odit aut fugit, sed quia consequuntur magni dolores eos qui ratione voluptatem sequi nesciunt.</p>
  <article class="card" style="left:140px"><div class="placeholder" role="img" aria-label="Analyst working at a laptop"></div><h5>Lorem ipsum dolor sit amet, consectetur</h5><div class="date">Feb 27, 2018</div><p>Lorem ipsum dolor sit amet, consectetur adipiscing elit, sed do tempor incididunt ut labore.</p><div class="more">Read more &rsaquo;</div></article>
  <article class="card" style="left:474px"><div class="placeholder" role="img" aria-label="Investor reviewing reports at a desk"></div><h5>Lorem ipsum dolor sit amet, consectetur</h5><div class="date">Feb 28, 2018</div><p>Lorem ipsum dolor sit amet, consectetur adipiscing elit, sed do tempor incididunt ut labore.</p><div class="more">Read more &rsaquo;</div></article>
  <article class="card" style="left:797px"><div class="placeholder" role="img" aria-label="Engineer typing on a laptop"></div><h5>Lorem ipsum dolor sit amet, consectetur</h5><div class="date">March 21, 2018</div><p>Lorem ipsum dolor sit amet, consectetur adipiscing elit, sed do tempor incididunt ut labore.</p><div class="more">Read more &rsaquo;</div></article>
</section>

<section class="section newsletter">
  <div class="abs label">Subscribe to our <b>NEWSLETTER</b></div>
  <div class="abs input">Enter your email address</div>
  <div class="abs submit">Subscribe</div>
</section>

<section class="section feedback">
  <h2 class="section-title" style="top:54px">Feedback From <b>Investors</b></h2>
  <div class="rule" style="top:112px"></div>
  <div class="abs arrow" style="left:140px">&lsaquo;</div>
  <div class="abs avatar" role="img" aria-label="Investor portrait"></div>
  <div class="abs who">Maren Holt<span>INVESTOR</span></div>
  <p class="abs quote">Lorem ipsum dolor sit amet, consectetur adipiscing elit, sed do eiusmod tempor incididunt ut labore et dolore magna aliqua. Ut enim ad minim veniam, quis nostrud exercitation ullamco laboris nisi ut aliquip ex ea commodo.</p>
  <div class="abs arrow" style="left:1064px">&rsaquo;</div>
  <div class="abs dots" style="left:585px;top:340px"><span class="on"></span><span></span></div>
</section>

<footer class="section footer">
  <div class="abs brand" style="left:80px;top:60px"><div class="brand-dot" style="width:38px;height:38px"></div><div class="brand-name" style="color:#fff;font-size:20px">Tidal Forge</div></div>
  <p class="abs" style="left:80px;top:130px;width:240px;line-height:17px">Lorem ipsum dolor sit amet, consectetur adipiscing elit, sed do tempor incididunt ut labore et dolore magna aliqua.</p>
  <div class="abs" style="left:80px;top:210px;line-height:26px">&#9742; 416-555-0192<br>&#9993; hello@tidalforge.example<br>&#9679; www.tidalforge.example</div>
  <div class="vline" style="left:356px"></div>
  <h6 style="left:386px">OUR SERVICES</h6>
  <ul style="left:386px;top:112px"><li>&rsaquo; Vix no quem periculis</li><li>&rsaquo; Quo ne exerci dolorem</li><li>&rsaquo; Nec sumo aeque tempor</li><li>&rsaquo; Populo illum verear</li><li>&rsaquo; Accumsan an nec ius</li><li>&rsaquo; Mucius argumentum</li></ul>
  <div class="vline" style="left:612px"></div>
  <h6 style="left:642px">RECENT POST</h6>
  <div class="post" style="top:112px"><div class="thumb" role="img" aria-label="Gold coin thumbnail"></div><div class="t"><b>27 Feb 2018</b>Lorem ipsum dolor sit amet, consectetur adipiscing</div></div>
  <div class="post" style="top:180px"><div class="thumb" role="img" aria-label="Gold coin thumbnail"></div><div class="t"><b>15 Mar 2018</b>Lorem ipsum dolor sit amet, consectetur adipiscing</div></div>
  <div class="post" style="top:248px"><div class="thumb" role="img" aria-label="Gold coin thumbnail"></div><div class="t"><b>21 Mar 2018</b>Lorem ipsum dolor sit amet, consectetur adipiscing</div></div>
  <div class="vline" style="left:903px"></div>
  <h6 style="left:933px">FOLLOW US ON</h6>
  <div class="social"><span></span><span></span><span></span><span></span></div>
  <h6 style="left:933px;top:210px">CALL US ON</h6>
  <div class="abs" style="left:933px;top:236px;font-size:24px;font-weight:700;color:#fff">416-555-0192</div>
</footer>

<div class="section copyright">&copy; 2017 Tidal Forge &nbsp;|&nbsp; Privacy Policy &nbsp;|&nbsp; User Agreement</div>

</body>
</html>
```